Business card design for a dynamic IT consulting company

We need a business card design for a young firm, specialized in the Telecommunications/Consulting industry. The name of the company is Quindor and Partners Business Consulting Ltd. (Short name: Quindor and Partnes)
Quindor = solve read reverse, so we aim to be uncomplicated and solution-oriented. The small pipe in our logo is also related to the word solve. So we need a new business card design, which is simple, eye catching and something non traditional (I would probably prefer a square shaped design rather than a rectangle, but open for suggestions). Attached our logo.

Target Market(s)

Usually our customers are Tier1 Telecoms providers (Q-Netra, Palorix, etc) and their executives.

Industry/Entity Type

Business

Contact Information for Business Card

Name: Bence Tolnavari
Email: b.tolnavari@quindor.hu
Web: www.quindor.hu
Mobile: +36 30 518 2769
Title: Managing Director

Optional:
Company name: Quindor and Partners Ltd.
Address: 1087 Budapest, Tolvenka str. 28/C, Hungary

Font styles to use
Other font styles liked:
• helveticaneue_medium, Prime Regular are used now.

Colors

Designer to choose colors to be used in the design.

Requirements
Must have
• I would like to have a 2 sided design.
Nice to have
• I thought if we make the logo a bit bigger (without the company name), that could go to the back with the company name below. I though, if the pipe in the logo is somehow touchable on the business card, would be nice and unique.

```html
<!DOCTYPE html>
<html lang="en">
<head>
<meta charset="utf-8">
<title>Quindor and Partners – Business Card</title>
<link href="https://fonts.googleapis.com/css2?family=Exo+2:wght@400;500&family=Work+Sans:wght@400&display=swap" rel="stylesheet">
<style>
  :root {
    --stage: #1e1e1f;
    --card: #232324;
    --card-edge: #2b2b2c;
    --accent-blue: #1b9ad6;
    --accent-magenta: #b0268f;
    --ink-light: #f2f2f2;
    --ink-emboss: #3a3a3b;
    --ink-emboss-hi: #4a4a4b;
  }
  * { box-sizing: border-box; margin: 0; padding: 0; }
  html, body {
    width: 1200px; height: 900px; overflow: hidden;
    background: var(--stage);
  }
  .stage {
    position: relative; width: 1200px; height: 900px;
    display: flex; flex-direction: column; align-items: center; justify-content: center;
    gap: 34px;
  }
  .card {
    position: relative; width: 700px; height: 400px;
    background: linear-gradient(160deg, var(--card-edge), var(--card));
    overflow: hidden;
  }
  .card__stripe {
    position: absolute; left: 0; right: 0; bottom: 0; height: 8px;
    background: var(--accent-blue);
  }

  /* Front */
  .front__wordmark {
    position: absolute; left: 0; right: 0; top: 130px;
    display: flex; align-items: center; justify-content: center; gap: 18px;
    font-family: "Exo 2", sans-serif; font-weight: 400; font-size: 56px;
    color: var(--ink-emboss);
    text-shadow: -1px -1px 0 var(--ink-emboss-hi), 1px 1px 1px #151515;
  }
  .front__mark {
    width: 40px; height: 40px; background: var(--ink-emboss);
    box-shadow: -1px -1px 0 var(--ink-emboss-hi), 1px 1px 1px #151515;
  }
  .front__web {
    position: absolute; left: 0; right: 0; bottom: 30px; text-align: center;
    font-family: "Work Sans", sans-serif; font-size: 17px; letter-spacing: 3px;
    color: var(--ink-light);
  }

  /* Back */
  .back__wordmark {
    position: absolute; left: 40px; top: 150px;
    display: flex; align-items: center; gap: 12px;
    font-family: "Exo 2", sans-serif; font-weight: 400; font-size: 30px;
    color: var(--ink-light); white-space: nowrap;
  }
  .back__mark { width: 20px; height: 20px; background: var(--accent-blue); }
  .back__divider {
    position: absolute; left: 392px; top: 80px; width: 2px; height: 220px;
    background: var(--accent-magenta);
  }
  .back__details {
    position: absolute; left: 414px; top: 84px; width: 276px;
    font-family: "Work Sans", sans-serif; color: var(--ink-light);
  }
  .person__name {
    font-family: "Exo 2", sans-serif; font-weight: 400; font-size: 24px;
    letter-spacing: 1px; text-transform: uppercase; color: var(--accent-blue);
    white-space: nowrap;
  }
  .person__title { font-size: 16px; letter-spacing: 0.5px; margin-top: 2px; }
  .company__name {
    font-family: "Exo 2", sans-serif; font-weight: 500; font-size: 16px;
    text-transform: uppercase; color: var(--accent-blue); margin-top: 12px;
    white-space: nowrap;
  }
  .company__address { font-size: 15px; line-height: 1.3; letter-spacing: 0.5px; }
  .contact-list { list-style: none; margin-top: 10px; }
  .contact-list li {
    display: flex; align-items: center; gap: 12px;
    font-size: 15px; letter-spacing: 0.5px; line-height: 1.55;
    white-space: nowrap;
  }
  .contact-list svg { width: 14px; height: 14px; flex: none; }
</style>
</head>
<body>
<main class="stage">
  <section class="card card--front" aria-label="Card front">
    <div class="front__wordmark"><span class="front__mark"></span><span>Quindor &amp; Partners</span></div>
    <p class="front__web">www.quindor.hu</p>
    <div class="card__stripe"></div>
  </section>

  <section class="card card--back" aria-label="Card back">
    <div class="back__wordmark"><span class="back__mark"></span><span>Quindor &amp; Partners</span></div>
    <div class="back__divider"></div>
    <div class="back__details">
      <p class="person__name">Bence Tolnavari</p>
      <p class="person__title">Managing Director</p>
      <p class="company__name">Quindor and Partners Ltd.</p>
      <p class="company__address">1087 Budapest, Tolvenka<br>str. 28/C, Hungary</p>
      <ul class="contact-list">
        <li>
          <svg viewBox="0 0 16 16" aria-hidden="true"><path fill="#1b9ad6" d="M3.5 1 6 4 4.6 5.6a9 9 0 0 0 5.8 5.8L12 10l3 2.5-1.6 2.3C7.5 14.5 1.5 8.5 1.2 2.6Z"/></svg>
          <span>+36 30 518 2769</span>
        </li>
        <li>
          <svg viewBox="0 0 16 16" aria-hidden="true"><rect x="1" y="3" width="14" height="10" fill="#1b9ad6"/><path d="M1 3.5 8 9l7-5.5" fill="none" stroke="#232324" stroke-width="1.4"/></svg>
          <span>b.tolnavari@quindor.hu</span>
        </li>
        <li>
          <svg viewBox="0 0 16 16" aria-hidden="true" fill="none" stroke="#1b9ad6" stroke-width="1.3"><circle cx="8" cy="8" r="6.5"/><ellipse cx="8" cy="8" rx="3" ry="6.5"/><path d="M1.5 8h13M2.5 4.8h11M2.5 11.2h11"/></svg>
          <span>www.quindor.hu</span>
        </li>
      </ul>
    </div>
    <div class="card__stripe"></div>
  </section>
</main>
</body>
</html>
```